Brightwave Reach - Business Card

We need a business card for a Social Media Marketing company that specializes in online marketing for small businesses in Canada using common Social Media platforms such as Pixlora, Chatterly, Blinkpost & Quibber.

I have uploaded a copy of our logo which I would like utilized in the business card. We would like the business card to be modern yet classy design.

Our website is www.brightwavereach.ca

Industry/Entity Type

Marketing

Contact Information for Business Card

Email: info@brightwavereach.ca
Website: www.brightwavereach.ca
Telephone: 604-555-0193

Colors

Designer to choose colors to be used in the design.

Requirements
Must have
• Social Media icons on reverse
• Please add some designs with color.

```html
<!DOCTYPE html>
<html lang="en">
<head>
<meta charset="utf-8">
<title>Brightwave Reach – Business Card</title>
<link rel="stylesheet" href="https://fonts.googleapis.com/css2?family=Arimo:wght@400;700&display=swap">
<style>
  :root {
    --backdrop: #4b4b4b;
    --front-top: #ffffff;
    --front-bottom: #dcdcdc;
    --back-card: #3b3e41;
    --ink-dark: #3a3a3a;
    --ink-light: #e6e6e6;
    --icon-tile: #d9d9d9;
  }
  html, body {
    margin: 0;
    padding: 0;
    width: 1200px;
    height: 965px;
    overflow: hidden;
    background: var(--backdrop);
    font-family: "Arimo", Arial, sans-serif;
  }
  .canvas { position: relative; width: 1200px; height: 965px; }
  .card {
    position: absolute;
    left: 277px;
    width: 648px;
    height: 368px;
    box-shadow: 0 3px 10px rgba(0,0,0,0.45);
  }
  .card--front {
    top: 97px;
    background: radial-gradient(ellipse at 50% 10%, var(--front-top) 0%, var(--front-top) 35%, var(--front-bottom) 100%);
    color: var(--ink-dark);
  }
  .card--back {
    top: 502px;
    background: var(--back-card);
    color: var(--ink-light);
  }
  .brand {
    position: absolute;
    display: flex;
    flex-direction: column;
    align-items: center;
    text-align: center;
    font-weight: 700;
    text-transform: uppercase;
  }
  .brand__name { font-size: 25px; line-height: 27px; letter-spacing: 0.5px; }
  .brand__mark {
    width: 12px; height: 12px;
    margin-top: 10px;
    background: currentColor;
  }
  .brand__initials { font-size: 11px; margin-top: 6px; letter-spacing: 1px; }
  .card--front .brand { left: 82px; top: 125px; width: 175px; }
  .card--back .brand { left: 222px; top: 127px; width: 204px; }
  .card--back .brand__name { font-size: 29px; line-height: 31px; }

  .person { position: absolute; left: 384px; top: 124px; }
  .person__name { font-size: 20px; letter-spacing: 0.5px; margin: 0; font-weight: 400; text-transform: uppercase; }
  .person__role { font-size: 14px; margin: 4px 0 0 3px; }
  .contacts { list-style: none; margin: 0; padding: 0; position: absolute; left: 384px; top: 190px; font-size: 14px; }
  .contacts li { display: flex; align-items: center; height: 19px; }
  .contacts svg { width: 12px; height: 12px; margin-right: 7px; stroke: var(--ink-dark); fill: none; stroke-width: 1.3; }

  .socials { position: absolute; top: 321px; left: 246px; display: flex; gap: 12px; }
  .socials span { width: 30px; height: 30px; background: var(--icon-tile); display: block; }
</style>
</head>
<body>
<div class="canvas">
  <section class="card card--front" aria-label="Card front">
    <div class="brand">
      <div class="brand__name">Brightwave<br>Reach</div>
      <div class="brand__mark"></div>
      <div class="brand__initials">BWR</div>
    </div>
    <div class="person">
      <h1 class="person__name">Alex Morgan</h1>
      <p class="person__role">Managing Director</p>
    </div>
    <ul class="contacts">
      <li><svg viewBox="0 0 12 12"><path d="M2 1.5 L4 1.5 L5 4 L3.8 5 Q5 7.5 7 8.2 L8 7 L10.5 8 L10.5 10 Q5 11 1.5 3.5 Z"/></svg>604-555-0193</li>
      <li><svg viewBox="0 0 12 12"><rect x="1" y="2.5" width="10" height="7"/><path d="M1 2.5 L6 6.5 L11 2.5"/></svg>info@brightwavereach.ca</li>
      <li><svg viewBox="0 0 12 12"><circle cx="6" cy="6" r="5"/><ellipse cx="6" cy="6" rx="2.2" ry="5"/><path d="M1 6 H11"/></svg>www.brightwavereach.ca</li>
    </ul>
  </section>

  <section class="card card--back" aria-label="Card back">
    <div class="brand">
      <div class="brand__name">Brightwave<br>Reach</div>
      <div class="brand__mark"></div>
      <div class="brand__initials">BWR</div>
    </div>
    <div class="socials">
      <span role="img" aria-label="Chatterly profile"></span>
      <span role="img" aria-label="Quibber profile"></span>
      <span role="img" aria-label="Pixlora profile"></span>
      <span role="img" aria-label="Linkora profile"></span>
    </div>
  </section>
</div>
</body>
</html>
```